New Fun, Positive, energised looking Business Card Needed for High Achiever Coach

I am looking for a two sided full colour business card. I am self employed and have recently re branded my 1-2-1 work re-vitalising high achievers. My target client base for these cards is therefore high achievers - usually aged 40 -55, they are often entrepreneurs, CEO or work in banking and finance and 2/3 are male. I work with them on 90 day or 6 month coaching programs to help them live their success in a healthier, more sustainable and fulfiiled way. They pay for this privately so though they are corporate types the cards need not look 'corporate'. I want to portray the idea of transformation, vitality and re-connecting.
You can get a feel for the look I like on my new website: morvenlisk.co.uk
I want to use this logo with strapline (Re-Vitalising High Achievers) (I purchased off Logoharbor) and font/ colours (the turquoise and green).
Details to include on the card:
www.morvenlisk.co.uk
+44 7915 302618
morven@morvenlisk.co.uk
skype: morvenlisk
I'd also like to include:
Do you struggle to switch off? Want to be healthier and feel fitter? Want closer relationships? More clarity over the direction you are headed? I can help you do these things using integrated mind-body techniques. Visit morvenlisk.co.uk TODAY to apply for a FREE Breakthrough session.
BUT if that is too much text for a card I am open to advice/ammendments.
Updates
Thanks for your design - I am considering them. PLease change the wording to :

```html
<!DOCTYPE html>
<html lang="en">
<head>
<meta charset="utf-8">
<title>Morven Lisk – Business Card</title>
<link rel="stylesheet" href="https://fonts.googleapis.com/css2?family=Source+Sans+3:wght@400;700&display=swap">
<style>
  :root {
    --backdrop: #6b6c6f;
    --card-white: #ffffff;
    --brand-turquoise: #2ba7cb;
    --band-blue: #45bfe0;
    --brand-green: #63bd68;
    --back-turquoise: #0aa5ca;
    --link-green: #9bd13f;
    --text-white: #ffffff;
  }
  * { box-sizing: border-box; margin: 0; padding: 0; }
  html, body {
    width: 1200px;
    height: 1022px;
    overflow: hidden;
    background: var(--backdrop);
  }
  .canvas {
    position: relative;
    width: 1200px;
    height: 1022px;
    background: var(--backdrop);
  }
  .card {
    position: absolute;
    border-radius: 36px;
    overflow: hidden;
  }

  /* Front */
  .card-front {
    left: 18px; top: 59px;
    width: 536px; height: 935px;
    background: var(--card-white);
    border: 1px solid #d6d6d6;
  }
  .front-wave {
    position: absolute;
    left: 0; top: 0;
    width: 536px; height: 935px;
  }
  .brand-mark {
    position: absolute;
    left: 50%; top: 30px;
    width: 150px; height: 150px;
    margin-left: -75px;
    border-radius: 50%;
    background: var(--brand-green);
  }
  .brand-name {
    position: absolute;
    left: 0; right: 0; top: 232px;
    text-align: center;
    font-family: "Source Sans 3", sans-serif;
    font-weight: 700;
    font-size: 50px;
    line-height: 60px;
    color: var(--brand-turquoise);
  }
  .contact-list {
    position: absolute;
    left: 26px; top: 762px;
    list-style: none;
    font-family: "Source Sans 3", sans-serif;
    font-size: 26px;
    color: var(--text-white);
  }
  .contact-item {
    display: flex;
    align-items: center;
    height: 34px;
  }
  .contact-icon {
    width: 24px; height: 24px;
    margin-right: 12px;
    flex: none;
  }

  /* Back */
  .card-back {
    left: 616px; top: 62px;
    width: 532px; height: 929px;
    background: var(--back-turquoise);
  }
  .pitch {
    position: absolute;
    left: 24px; right: 24px; top: 28px;
    text-align: center;
    font-family: "Source Sans 3", sans-serif;
    font-size: 24px;
    line-height: 30px;
    color: var(--text-white);
  }
  .pitch-link {
    color: var(--link-green);
    font-weight: 700;
  }
</style>
</head>
<body>
<main class="canvas">

  <section class="card card-front" aria-label="Business card front">
    <svg class="front-wave" viewBox="0 0 536 935" aria-hidden="true">
      <path d="M0 400 C 120 360, 360 400, 536 540 L536 935 L0 935 Z" fill="var(--band-blue)"/>
      <path d="M0 412 C 120 374, 360 414, 536 556 L536 935 L0 935 Z" fill="var(--brand-green)"/>
    </svg>

    <div class="brand-mark" aria-hidden="true"></div>
    <h1 class="brand-name">Morven Lisk</h1>

    <ul class="contact-list">
      <li class="contact-item">
        <svg class="contact-icon" viewBox="0 0 24 24" aria-hidden="true">
          <path d="M3 9 C3 5 21 5 21 9 L18 11 L15 9 L9 9 L6 11 Z" fill="#fff"/>
          <path d="M7 11 L17 11 L20 20 L4 20 Z" fill="#fff"/>
        </svg>
        +44 7915 302618
      </li>
      <li class="contact-item">
        <svg class="contact-icon" viewBox="0 0 24 24" aria-hidden="true">
          <circle cx="12" cy="12" r="10" fill="#fff"/>
        </svg>
        morvenlisk
      </li>
      <li class="contact-item">
        <svg class="contact-icon" viewBox="0 0 24 24" aria-hidden="true">
          <circle cx="12" cy="12" r="10" fill="#fff"/>
          <g fill="none" stroke="var(--brand-green)" stroke-width="1.6">
            <ellipse cx="12" cy="12" rx="4" ry="10"/>
            <line x1="2" y1="12" x2="22" y2="12"/>
            <line x1="4" y1="7" x2="20" y2="7"/>
            <line x1="4" y1="17" x2="20" y2="17"/>
          </g>
        </svg>
        www.morvenlisk.co.uk
      </li>
      <li class="contact-item">
        <svg class="contact-icon" viewBox="0 0 24 24" aria-hidden="true">
          <rect x="2" y="5" width="20" height="14" fill="#fff"/>
          <path d="M2 5 L12 13 L22 5" fill="none" stroke="var(--brand-green)" stroke-width="1.6"/>
        </svg>
        morven@morvenlisk.co.uk
      </li>
    </ul>
  </section>

  <section class="card card-back" aria-label="Business card back">
    <p class="pitch">
      Do you struggle to switch off? Want to be<br>
      healthier and feel fitter? Want closer<br>
      relationships? More clarity over the direction<br>
      you are headed? I can help you do these<br>
      things using integrated mind-body<br>
      techniques.<br>
      Visit <span class="pitch-link">morvenlisk.co.uk</span><br>
      TODAY to apply for a FREE Breakthrough<br>
      session.
    </p>
  </section>

</main>
</body>
</html>
```